Coastline Premier Retreats Business Card Design

Design a business card for Coastline Premier Retreats. Look at the website for colors and reference. Card should have logo, name, title, office number, mobile number, email, URL and a tagline like, "Luxury Hotel & Resort Email Marketing" (This might change).

https://www.coastlinepremierretreats.example

The rest I will leave up to your imagination.

Contact Information for Business Card

Logo, name, title, office number, mobile number, email, URL and a tagline like, "Luxury Hotel & Resort Email Marketing" (This might change).

```html
<!DOCTYPE html>
<html lang="en">
<head>
<meta charset="utf-8">
<title>Coastline Premier Retreats – Business Card</title>
<link rel="stylesheet" href="https://fonts.googleapis.com/css2?family=Montserrat:wght@400;500;700;800&display=swap">
<style>
  :root {
    --bg: #2b2b2b;
    --card: #1b1b1b;
    --orange: #f07a14;
    --white: #f2f2f2;
    --muted: #6d6d6d;
  }
  * { box-sizing: border-box; margin: 0; padding: 0; }
  html, body { width: 1200px; height: 1200px; overflow: hidden; }
  body {
    background: var(--bg);
    font-family: "Montserrat", sans-serif;
    display: flex;
    align-items: center;
    justify-content: center;
    gap: 60px;
  }
  .card {
    width: 480px;
    height: 840px;
    background: var(--card);
    border-radius: 28px;
    position: relative;
    color: var(--white);
    box-shadow: 0 18px 40px rgba(0,0,0,.45);
  }
  /* front */
  .card-front { display: flex; flex-direction: column; align-items: center; padding: 90px 40px 0; text-align: center; }
  .brand { display: flex; align-items: center; gap: 14px; }
  .brand-mark { width: 22px; height: 22px; background: var(--orange); flex: none; }
  .brand-name { font-weight: 800; font-size: 25px; text-transform: uppercase; letter-spacing: .5px; color: var(--white); line-height: 1.2; text-align: left; }
  .person { margin-top: 170px; }
  .person-name { color: var(--orange); font-weight: 800; font-size: 40px; text-transform: uppercase; letter-spacing: 1px; }
  .person-title { font-size: 22px; font-weight: 400; margin-top: 4px; }
  .icon-row { display: flex; align-items: center; gap: 10px; margin-top: 44px; width: 100%; }
  .rule { flex: 1; height: 2px; background: var(--orange); }
  .icon { width: 30px; height: 30px; border-radius: 50%; background: var(--orange); display: flex; align-items: center; justify-content: center; }
  .contacts { margin-top: 18px; font-size: 20px; line-height: 1.55; }
  .contacts .accent { color: var(--orange); }
  .divider { width: 100%; height: 2px; background: var(--orange); margin: 22px 0 20px; }
  .address { font-size: 20px; line-height: 1.5; }
  /* back */
  .card-back { overflow: hidden; }
  .back-brand {
    position: absolute; left: 44%; top: 50%;
    width: 640px;
    transform: translate(-50%, -50%) rotate(-90deg);
    display: flex; align-items: center; justify-content: center; gap: 20px;
  }
  .back-brand .brand-mark { width: 36px; height: 36px; background: var(--muted); }
  .back-brand .brand-name { font-size: 44px; line-height: 1.1; color: var(--muted); white-space: nowrap; }
  .tagline {
    position: absolute; left: 82%; top: 50%;
    transform: translate(-50%, -50%) rotate(-90deg);
    color: var(--orange); font-size: 22px; font-weight: 400; white-space: nowrap;
  }
</style>
</head>
<body>
  <section class="card card-front">
    <div class="brand">
      <span class="brand-mark"></span>
      <span class="brand-name">Coastline Premier<br>Retreats</span>
    </div>
    <div class="person">
      <h1 class="person-name">Daniel Hart</h1>
      <p class="person-title">CEO/Founder</p>
    </div>
    <div class="icon-row">
      <span class="rule"></span>
      <span class="icon" aria-label="mobile">
        <svg width="14" height="16" viewBox="0 0 14 16"><rect x="3" y="1" width="8" height="14" rx="1.5" fill="none" stroke="#1b1b1b" stroke-width="1.6"/></svg>
      </span>
      <span class="icon" aria-label="office phone">
        <svg width="16" height="16" viewBox="0 0 16 16"><path d="M2 6c0-2 2-3 6-3s6 1 6 3l-2 1-1-2H5L4 7zM3 9h10v4H3z" fill="#1b1b1b"/></svg>
      </span>
      <span class="icon" aria-label="email">
        <svg width="16" height="14" viewBox="0 0 16 14"><rect x="1" y="2" width="14" height="10" fill="none" stroke="#1b1b1b" stroke-width="1.6"/><path d="M1 2l7 6 7-6" fill="none" stroke="#1b1b1b" stroke-width="1.6"/></svg>
      </span>
      <span class="icon" aria-label="website">
        <svg width="16" height="16" viewBox="0 0 16 16"><circle cx="8" cy="8" r="6.5" fill="none" stroke="#1b1b1b" stroke-width="1.4"/><ellipse cx="8" cy="8" rx="3" ry="6.5" fill="none" stroke="#1b1b1b" stroke-width="1.2"/><path d="M1.5 8h13" stroke="#1b1b1b" stroke-width="1.2"/></svg>
      </span>
      <span class="rule"></span>
    </div>
    <div class="contacts">
      <p>555.014.2290</p>
      <p>+34 600 000 417</p>
      <p>info@coastlinepremierretreats.example</p>
      <p>www.<span class="accent">coastlinepremierretreats</span>.example</p>
    </div>
    <div class="divider"></div>
    <div class="address">
      <p>Po Box, 48 B Harbor Rd</p>
      <p>Seaview, AB 10452</p>
    </div>
  </section>

  <section class="card card-back">
    <div class="back-brand">
      <span class="brand-mark"></span>
      <span class="brand-name">Coastline Premier<br>Retreats</span>
    </div>
    <p class="tagline">Luxury Hotel &amp; Resort Email Marketing</p>
  </section>
</body>
</html>
```